Cat-products company needs smart, yet endearing, business card

We need a business card design for a new, but up-and-running, business based in Honolulu, Hawaii. The business is Purrnest Nook Co. Our first product is the most environmentally-friendly cat grass kit ever seen on the planet. Future products, currently in the R&D phase, will include a variety of exciting cat scratchers. We also do consulting work to help apartment-dwellers make their home more cat-friendly and, in the future, plan on doing full, custom installs of structure to create high walkways for cats.

Target Market(s)

Middle-aged, apartment-dwelling, middle-class workers who own 1 or more cats and who dote on them.

Industry/Entity Type

Pet Care

Contact Information for Business Card

A striking, professional, yet warm and friendly design is what we're after.

Font styles to use
Serif
Sans Serif
Other font styles liked:
• Comfortaa

Colors

Designer to choose colors to be used in the design.

Requirements
Must have
• The company logo: (see attachment)
• The company name: Purrnest Nook Co
• The web address: www.purrnestnookco.com
• Email: support@purrnestnookco.com
• Phone: +1 (808) 571 6023
• Update (Fri Jun 30 3017 7:45pm Hawaii Time) I would like, is possible, uploaded picture of the cat grass kit on the back of the card with some text along the lines of: Purrnest Nook Co - Maker Of The Leafiest Feline Sprout Set Yet
Nice to have
• A cat picture, cartoon, real or silhouette that illustrates cats in action and/or relaxing; ie using the apartment space to live, play and relax in and being well-contented.
• Most of the website is done in the font: Comfortaa. It might be nice to continue using this for brand consistency.
Should not have
• Hard-to-read fonts.

```html
<!DOCTYPE html>
<html lang="en">
<head>
<meta charset="utf-8">
<title>Purrnest Nook Co — Business Card</title>
<link rel="stylesheet" href="https://fonts.googleapis.com/css2?family=Comfortaa:wght@700&family=Oswald:wght@400;500&family=Roboto:wght@400;500&display=swap">
<style>
  :root {
    --backdrop: #2c2c2e;
    --card: #1e1e20;
    --cocoa: #6e4339;
    --honey: #f4c01a;
    --ink-light: #f2f2f2;
    --dot: #4a4a4e;
    --divider: #d8d8d8;
  }
  * { box-sizing: border-box; margin: 0; padding: 0; }
  html, body {
    width: 1200px; height: 900px; overflow: hidden;
    background: var(--backdrop);
  }
  .canvas {
    width: 1200px; height: 900px;
    display: flex; flex-direction: column; align-items: center; justify-content: center;
    gap: 36px;
  }
  .card {
    position: relative;
    width: 740px; height: 400px;
    background: var(--card);
    box-shadow: 0 10px 24px rgba(0,0,0,.45);
  }

  /* Front */
  .social-dots {
    position: absolute; top: 22px; right: 24px;
    display: flex; gap: 6px;
  }
  .social-dots span {
    width: 20px; height: 20px; border-radius: 50%;
    background: var(--dot);
  }
  .brand {
    position: absolute; top: 112px; left: 0; right: 0;
    display: flex; flex-direction: column; align-items: center; gap: 18px;
  }
  .brand-mark {
    width: 64px; height: 64px; background: var(--cocoa);
  }
  .brand-name {
    font-family: "Comfortaa", sans-serif; font-weight: 700;
    font-size: 40px; color: var(--honey); letter-spacing: 1px;
  }
  .front-url {
    position: absolute; top: 300px; left: 0; right: 0; text-align: center;
    font-family: "Roboto", sans-serif; font-size: 17px; font-weight: 500;
    letter-spacing: 6px; color: var(--ink-light);
  }
  .front-url .domain { color: var(--honey); }

  /* Back */
  .identity {
    position: absolute; top: 120px; right: 420px; text-align: right;
  }
  .person-name {
    font-family: "Oswald", sans-serif; font-weight: 400;
    font-size: 40px; color: var(--cocoa); line-height: 1.1; letter-spacing: .5px;
  }
  .person-role {
    font-family: "Roboto", sans-serif; font-weight: 500;
    font-size: 18px; color: var(--honey); margin-top: 4px;
  }
  .divider {
    position: absolute; top: 112px; left: 345px;
    width: 2px; height: 96px;
    background: linear-gradient(to bottom, transparent, var(--divider), transparent);
  }
  .contacts {
    position: absolute; top: 124px; left: 380px;
    list-style: none;
    font-family: "Roboto", sans-serif; font-size: 18px; color: var(--ink-light);
  }
  .contacts li { display: flex; align-items: center; gap: 10px; line-height: 26px; }
  .contacts svg, .address svg { flex: none; fill: var(--cocoa); }
  .address {
    position: absolute; top: 315px; left: 150px;
    display: flex; align-items: center; gap: 8px;
    font-family: "Roboto", sans-serif; font-size: 19px; color: var(--ink-light);
  }
</style>
</head>
<body>
<main class="canvas">
  <section class="card card-front">
    <div class="social-dots" aria-hidden="true"><span></span><span></span><span></span><span></span></div>
    <div class="brand">
      <div class="brand-mark" aria-hidden="true"></div>
      <div class="brand-name">Purrnest Nook Co</div>
    </div>
    <p class="front-url">www.<span class="domain">purrnestnookco</span>.com</p>
  </section>

  <section class="card card-back">
    <div class="identity">
      <h1 class="person-name">KAI MALONE</h1>
      <p class="person-role">CEO/FOUNDER</p>
    </div>
    <div class="divider" aria-hidden="true"></div>
    <ul class="contacts">
      <li>
        <svg width="14" height="14" viewBox="0 0 24 24" aria-hidden="true"><path d="M6.6 10.8a15 15 0 0 0 6.6 6.6l2.2-2.2c.3-.3.7-.4 1-.2 1.1.4 2.3.6 3.6.6.6 0 1 .4 1 1V20c0 .6-.4 1-1 1A17 17 0 0 1 3 4c0-.6.4-1 1-1h3.5c.6 0 1 .4 1 1 0 1.3.2 2.5.6 3.6.1.3 0 .7-.2 1z"/></svg>
        +1 (808) 571 6023
      </li>
      <li>
        <svg width="14" height="14" viewBox="0 0 24 24" aria-hidden="true"><path d="M2 5h20v14H2z M3 6l9 7 9-7" /><path d="M2 5l10 8 10-8v-.5H2z" fill="#1e1e20"/></svg>
        support@purrnestnookco.com
      </li>
      <li>
        <svg width="14" height="14" viewBox="0 0 24 24" aria-hidden="true"><circle cx="12" cy="12" r="10"/><path d="M2 12h20M12 2c3 3 3 17 0 20M12 2c-3 3-3 17 0 20" stroke="#1e1e20" stroke-width="1.6" fill="none"/></svg>
        www.purrnestnookco.com
      </li>
    </ul>
    <p class="address">
      <svg width="14" height="18" viewBox="0 0 24 30" aria-hidden="true"><path d="M12 0a10 10 0 0 0-10 10c0 7.5 10 20 10 20s10-12.5 10-20A10 10 0 0 0 12 0zm0 14a4 4 0 1 1 0-8 4 4 0 0 1 0 8z"/></svg>
      4120 Hibiscus Way, Honolulu, Hawaii 96815
    </p>
  </section>
</main>
</body>
</html>
```